Stationery Design Project

We need a stationery design for our Norwegian trucking company. We have existed for about 15 years and our 12 drivers uses relatively new vehicles to transport goods around in northern Norway. Long distance routes with fresh fish og food transport is our main operations.

We have already made alogo that's printed on our trucks. The logo and a picture of our trucks is attached. I think the logo i crappy, but since its already in use, changing it is not an option in this round. Still using a better colour scheme in the overall stationery and more interesting fonts is possible (altso in the logo).

Company details:
Name: Kjelvraket AS
Organisation nr 873 615 309
Post adress: 8642 Raudvik

I like minimalism and simplicity. I am avalibly for questions in normal GMT working hours either here or on mail: ivar@fjordlast.no

Reason: Hi. Im extending the deadline because I needed some time to find a vector file of our logo. Sorry for the inconvenience

Hi, and thanks for all your interest in the project. Some updates:

-          I have decided to commit to using one of the designs. Some designer will get the payment.

-          I have extended the deadline with 24 hours since I needed some time to find our firms vector logo (a slow Swedish man was holding me up)

-          We will not choose a design before the deadline. No need to rush.

-          We have received a lot of great design and think there is a need to specified the product we want to make:

o   Business Card for all our employers. I just need the design and will duplicate with the correct numbers and name myself. The information on should be: Logo, employer’s name, Phone number, email, website, Postal number and address. Use this as a template: logo, Leif Brattvoll, 47382066, Leif@fjordlast.no,, fjordlast.no, 8642 Raudvik. The order and placement of the information is your creative decision.

o   Stickers to put on the goods we travel. On the sticker the should be the following information: Logo, phone number, Tekst and link: Fraktæ av Kjelvraket. Ke du syns? Fjordlast.no/tilbakemelding (this means: Handled by Kjelvraket. What do you think Fjordlast.no/feedback -à the link will be a feedback form). The placement the information and size is your creative decision with some stings: we have been thinking of using Drukko for printing and see that a size about 6x6 cm, 8x5 or something like that. (with 3000 copies our budget is 200 punds). Any suggestions of other suppliers are welcome. Drukko price calculator http://www.drukkolabelhouse.co.uk/digital-litho-printing/printing-labels-tags/stickers/

o   Letterhead with logo, address, phone number and organizational number.

o   Envelopes with logo,address, phone number and organizational number.

Have a nice day.

 

 

• Using the blue colour in the logo and using a similar graphic approch.

```html
<!DOCTYPE html>
<html lang="no">
<head>
<meta charset="utf-8">
<title>Kjelvraket AS – Stationery</title>
<link rel="stylesheet" href="https://fonts.googleapis.com/css2?family=Exo+2:wght@400;600;700&family=Open+Sans:wght@400;700&family=Great+Vibes&display=swap">
<style>
  :root{
    --navy:#0b2f86;
    --blue:#1b74d0;
    --ink:#333;
    --text:#6a6a6a;
    --paper:#fff;
    --brand:'Exo 2', sans-serif;
    --body:'Open Sans', sans-serif;
    --accent-fill:linear-gradient(90deg,var(--blue) 0%,var(--navy) 100%);
  }
  *{margin:0;padding:0;box-sizing:border-box}
  html,body{width:1200px;height:900px;overflow:hidden}
  body{background:radial-gradient(ellipse at 50% 45%,#f7f7f7 0%,#e2e2e2 70%,#d6d6d6 100%);position:relative;font-family:var(--body)}
  .sheet{position:absolute;background:var(--paper);box-shadow:0 1px 5px rgba(0,0,0,.25);overflow:hidden}
  .accent-area{position:absolute;background:var(--accent-fill)}

  .brand{font-family:var(--brand);font-weight:700;color:var(--navy);display:flex;align-items:center;white-space:nowrap}
  .brand::before{content:"";display:inline-block;border-radius:50%;background:var(--blue)}

  .contact{position:absolute;font-family:var(--brand);color:var(--ink);border-left:1px solid var(--navy)}
  .contact .name{display:block}
  .contact li{list-style:none;display:flex;align-items:center}
  .contact svg{fill:var(--navy);flex:none}

  /* Letterhead */
  .letterhead{left:290px;top:12px;width:620px;height:876px}
  .letterhead .brand{position:absolute;left:42px;top:68px;font-size:36px}
  .letterhead .brand::before{width:22px;height:22px;margin-right:10px}
  .letterhead .contact{left:467px;top:50px;height:62px;padding-left:16px}
  .letterhead .contact .name{font-size:13px;margin-top:-1px;margin-bottom:5px}
  .letterhead .contact li{font-size:10px;height:15px;gap:7px}
  .letter-body{position:absolute;left:73px;top:212px;width:505px;font-size:11.3px;letter-spacing:-.1px;line-height:16.5px;color:var(--text)}
  .letter-body .greeting{font-weight:700;margin-bottom:20px;color:#555}
  .letter-body p{margin-bottom:16.5px}
  .signature{position:absolute;left:76px;top:662px;font-family:'Great Vibes',cursive;font-size:33px;color:#222}
  .role{position:absolute;left:76px;top:704px;font-size:12px;font-weight:700;color:#666}
  .letterhead .accent-area{left:0;right:0;bottom:0;height:26px}

  /* Sticker */
  .sticker{position:absolute;left:944px;top:84px;width:186px;height:186px;border-radius:50%;background:var(--paper);border:4px solid var(--navy);box-shadow:0 1px 5px rgba(0,0,0,.3);overflow:hidden;font-family:var(--brand);text-align:center}
  .sticker .handled{position:absolute;top:21px;width:100%;font-size:11px;color:var(--ink)}
  .sticker .brand{position:absolute;top:50px;left:0;right:0;justify-content:center;font-size:18px}
  .sticker .brand::before{width:11px;height:11px;margin-right:6px}
  .sticker .question{position:absolute;top:94px;width:100%;font-size:12.5px;color:var(--ink)}
  .sticker .link{position:absolute;top:110px;left:2px;width:176px;height:15px;background:var(--navy);color:#fff;font-size:10px;line-height:15px;clip-path:polygon(4% 0,100% 0,96% 100%,0 100%)}
  .sticker .phone{position:absolute;top:146px;left:48px;width:82px;height:11px;background:var(--blue);color:#fff;font-size:9px;line-height:11px;display:flex;justify-content:center;align-items:center;gap:4px;clip-path:polygon(8% 0,100% 0,92% 100%,0 100%)}
  .sticker .phone svg{fill:#fff}

  /* Business cards */
  .card{width:267px;height:147px;left:51px}
  .card-front{top:376px}
  .card-front .accent-area{left:0;top:0;bottom:0;width:46px}
  .card-front .brand{position:absolute;left:70px;top:58px;font-size:20px}
  .card-front .brand::before{width:12px;height:12px;margin-right:6px}
  .card-back{top:574px}
  .card-back .accent-area{right:0;top:0;bottom:0;width:40px}
  .card-back .brand{position:absolute;left:10px;top:20px;font-size:16px}
  .card-back .brand::before{width:10px;height:10px;margin-right:5px}
  .card-back .person{position:absolute;left:18px;top:84px;width:158px;font-family:var(--brand);font-size:11px;color:var(--ink);padding-bottom:5px;border-bottom:1px solid #8aa6d8}
  .card-back .details{position:absolute;left:17px;top:114px;display:grid;grid-template-columns:96px 90px;row-gap:3px;font-family:var(--brand);font-size:7.5px;color:var(--ink)}
  .card-back .details span{display:flex;align-items:center;gap:5px}
  .card-back .details svg{fill:var(--navy)}

  /* Envelope */
  .envelope{left:522px;top:376px;width:650px;height:325px}
  .envelope .brand{position:absolute;left:32px;top:38px;font-size:24px}
  .envelope .brand::before{width:15px;height:15px;margin-right:8px}
  .envelope .contact{left:246px;top:32px;height:48px;padding-left:13px}
  .envelope .contact .name{font-size:10px;margin-bottom:4px}
  .envelope .contact li{font-size:7.5px;height:12px;gap:5px}
  .envelope .accent-area{left:0;right:0;bottom:0;height:20px}
</style>
</head>
<body>

<section class="sheet letterhead">
  <div class="brand">Kjelvraket</div>
  <div class="contact">
    <span class="name">Kjelvraket AS</span>
    <ul>
      <li><svg width="8" height="8" viewBox="0 0 10 10"><rect x="1" y="0" width="8" height="10" rx="1"/><rect x="3" y="2" width="4" height="4" fill="#fff"/></svg>873 615 309</li>
      <li><svg width="8" height="9" viewBox="0 0 10 12"><path d="M5 0a4 4 0 0 1 4 4c0 3-4 8-4 8S1 7 1 4a4 4 0 0 1 4-4z"/><circle cx="5" cy="4" r="1.6" fill="#fff"/></svg>8642 Raudvik</li>
      <li><svg width="8" height="8" viewBox="0 0 10 10"><circle cx="5" cy="5" r="5"/><path d="M2 4h6M2 6h6M5 0v10" stroke="#fff" stroke-width=".8"/></svg>www.fjordlast.no</li>
    </ul>
  </div>
  <div class="letter-body">
    <p class="greeting">Lorem Ipsum,</p>
    <p>Cras mattis consectetur purus sit amet fermentum. Etiam porta sem malesuada magna mollis euismod. Integer posuere erat a ante venenatis dapibus posuere velit aliquet. Cras justo odio, dapibus ac facilisis in, egestas eget quam. Aenean eu leo quam. Pellentesque ornare sem lacinia quam venenatis vestibulum.</p>
    <p>Vivamus sagittis lacus vel augue laoreet rutrum faucibus dolor auctor. Donec sed odio dui. Etiam porta sem malesuada magna mollis euismod. Morbi leo risus, porta ac consectetur ac, vestibulum at eros. Nullam id dolor id nibh ultricies vehicula ut id elit.</p>
    <p>Donec id elit non mi porta gravida at eget metus. Fusce dapibus, tellus ac cursus commodo, tortor mauris condimentum nibh, ut fermentum massa justo sit amet risus. Cras justo odio, dapibus ac facilisis in, egestas eget quam. Parturient montes, nascetur ridiculus mus.</p>
    <p>Cum sociis natoque penatibus et magnis dis parturient montes, nascetur ridiculus mus. Morbi blandit tempus porttitor. Aenean lacinia bibendum nulla sed consectetur. Lorem ipsum dolor sit amet, consectetur adipiscing elit.</p>
    <p>Cras justo odio, dapibus ac facilisis in, egestas eget quam. Morbi leo risus, porta ac consectetur ac, vestibulum at eros. Duis mollis, est non commodo luctus, nisi erat porttitor ligula, eget odio sem nec elit. Integer posuere erat a ante venenatis dapibus. Vivamus sagittis lacus vel augue laoreet rutrum.</p>
  </div>
  <div class="signature">Your Name</div>
  <div class="role">Company Director</div>
  <div class="accent-area" role="img" aria-label="Decorative blue and navy band"></div>
</section>

<section class="sticker">
  <div class="handled">Fraktæ av</div>
  <div class="brand">Kjelvraket</div>
  <div class="question">KE DU SYNS?</div>
  <div class="link">Fjordlast.no/tilbakemelding</div>
  <div class="phone"><svg width="6" height="6" viewBox="0 0 10 10"><rect x="1" y="0" width="8" height="10" rx="1"/></svg>873 615 309</div>
</section>

<section class="sheet card card-front">
  <div class="accent-area" role="img" aria-label="Decorative blue and navy band"></div>
  <div class="brand">Kjelvraket</div>
</section>

<section class="sheet card card-back">
  <div class="accent-area" role="img" aria-label="Decorative blue and navy band"></div>
  <div class="brand">Kjelvraket</div>
  <div class="person">Leif Brattvoll</div>
  <div class="details">
    <span><svg width="6" height="6" viewBox="0 0 10 10"><rect x="1" y="0" width="8" height="10" rx="1"/></svg>47382066</span>
    <span><svg width="6" height="7" viewBox="0 0 10 12"><path d="M5 0a4 4 0 0 1 4 4c0 3-4 8-4 8S1 7 1 4a4 4 0 0 1 4-4z"/></svg>8642 Raudvik</span>
    <span><svg width="7" height="6" viewBox="0 0 12 9"><rect width="12" height="9" rx="1"/><path d="M0 0l6 5 6-5" stroke="#fff" fill="none"/></svg>Leif@fjordlast.no</span>
    <span><svg width="6" height="6" viewBox="0 0 10 10"><circle cx="5" cy="5" r="5"/></svg>www.fjordlast.no</span>
  </div>
</section>

<section class="sheet envelope">
  <div class="brand">Kjelvraket</div>
  <div class="contact">
    <span class="name">Kjelvraket AS</span>
    <ul>
      <li><svg width="6" height="6" viewBox="0 0 10 10"><rect x="1" y="0" width="8" height="10" rx="1"/></svg>873 615 309</li>
      <li><svg width="6" height="7" viewBox="0 0 10 12"><path d="M5 0a4 4 0 0 1 4 4c0 3-4 8-4 8S1 7 1 4a4 4 0 0 1 4-4z"/></svg>8642 Raudvik</li>
      <li><svg width="6" height="6" viewBox="0 0 10 10"><circle cx="5" cy="5" r="5"/></svg>www.fjordlast.no</li>
    </ul>
  </div>
  <div class="accent-area" role="img" aria-label="Decorative blue and navy band"></div>
</section>

</body>
</html>
```